Business Card Re-Design/Update

We'd like to update out business cards. I've included our current "Style guide" which has the colour scheme of the organisation in it. I've also included the branding files with logos etc in them.

I've also included a copy of one of our existing cards so that you can see how ugly/dated they look. I'd like a fresh modern corporate look.

Target Market(s)

These are for our clients, potential clients, industry contacts - like all business cards

Contact Information for Business Card

Name
Position
Company Address - Level 1, 47 Fernby Street, Carlow Qld 4072
Direct Phone
mobile
Email
Website -www.korvalit.com.au
Logo

Colors

Designer to choose colors to be used in the design.

Requirements
Must have
• Main Logo
• Cards will need to be editable to be able to personalize them for each new employee.
Nice to have
• The MapOut, ShipWell, KeepSteady would be okay to have if they can be sensibly and professionally added to the look without detracting from the main imagery.
• Maybe they could go on the back of the card? will leave this to your creative discretion as to whether/where they fit.
Should not have
• Should not have decorative or script fonts

```html
<!DOCTYPE html>
<html lang="en">
<head>
<meta charset="utf-8">
<title>korvalIT business card</title>
<link rel="stylesheet" href="https://fonts.googleapis.com/css2?family=Roboto:wght@400;700&family=Roboto+Condensed:wght@400;700&display=swap">
<style>
  :root {
    --backdrop: #e4e4e4;
    --card-white: #f7f7f7;
    --brand-red: #c8161d;
    --brand-red-deep: #9a0d13;
    --ink-dark: #231f20;
    --ink-text: #3a3a3a;
    --white: #ffffff;
  }
  html, body {
    margin: 0;
    padding: 0;
    width: 1200px;
    height: 960px;
    overflow: hidden;
    background: var(--backdrop);
    font-family: "Roboto", Arial, sans-serif;
  }
  .canvas { position: relative; width: 1200px; height: 960px; }

  .card { position: absolute; width: 600px; height: 342px; overflow: hidden; }

  /* Front */
  .card-front { left: 315px; top: 113px; background: var(--card-white); }
  .side-band {
    position: absolute; left: 45px; top: 0; width: 60px; height: 342px;
    background: linear-gradient(to bottom, var(--ink-dark) 0, var(--ink-dark) 62px, var(--brand-red) 62px, var(--brand-red-deep) 100%);
  }
  .front-brand {
    position: absolute; left: 52px; top: 60px;
    display: flex; align-items: center; gap: 14px;
  }
  .brand-square { width: 40px; height: 40px; background: var(--brand-red); }
  .brand-name {
    font-weight: 700; font-size: 33px; letter-spacing: -0.5px; color: var(--ink-dark);
  }
  .contact-icons {
    position: absolute; left: 67px; top: 146px; width: 16px; height: 160px;
  }
  .contact-icons svg { position: absolute; left: 0; width: 16px; height: 16px; fill: var(--white); }
  .contact-list {
    position: absolute; left: 129px; top: 145px;
    font-size: 14px; line-height: 19px; color: var(--ink-text);
  }
  .contact-list p { margin: 0; }
  .contact-list .address { margin-bottom: 8px; }
  .person {
    position: absolute; right: 37px; top: 203px; text-align: right;
    font-family: "Roboto Condensed", Arial, sans-serif;
  }
  .person-name { margin: 0; font-weight: 700; font-size: 20px; color: var(--brand-red); letter-spacing: 0.3px; }
  .person-title { margin: 2px 0 0; font-size: 14.5px; color: var(--ink-dark); }

  /* Back */
  .card-back {
    left: 311px; top: 472px;
    background: linear-gradient(to bottom, #d01a21 0%, var(--brand-red) 45%, var(--brand-red-deep) 100%);
  }
  .back-brand {
    position: absolute; left: 0; right: 0; top: 123px;
    display: flex; justify-content: center; align-items: center; gap: 20px;
  }
  .back-brand .brand-square { width: 62px; height: 62px; background: var(--white); }
  .back-brand .brand-name { font-size: 52px; color: var(--white); }
  .service-row {
    position: absolute; left: 0; right: 0; top: 276px;
    display: flex; justify-content: center; gap: 34px;
  }
  .service { display: flex; align-items: center; gap: 8px; color: var(--white); font-weight: 700; font-size: 25px; }
  .service-square { width: 22px; height: 22px; background: var(--white); }
</style>
</head>
<body>
<main class="canvas">
  <section class="card card-front" aria-label="Card front">
    <div class="side-band"></div>
    <div class="front-brand">
      <span class="brand-square"></span>
      <span class="brand-name">korvalIT</span>
    </div>
    <div class="contact-icons" aria-hidden="true">
      <svg style="top:0" viewBox="0 0 16 16"><path d="M8 1a5 5 0 0 0-5 5c0 3.6 5 9 5 9s5-5.4 5-9a5 5 0 0 0-5-5zm0 7a2 2 0 1 1 0-4 2 2 0 0 1 0 4z"/></svg>
      <svg style="top:45px" viewBox="0 0 16 16"><path d="M3.5 1.5l2.5 0 1.2 3.2-1.6 1.2a8 8 0 0 0 4.5 4.5l1.2-1.6 3.2 1.2v2.5c0 .8-.7 1.5-1.5 1.5C7 14 2 9 2 3c0-.8.7-1.5 1.5-1.5z"/></svg>
      <svg style="top:64px" viewBox="0 0 16 16"><path d="M3.5 1.5l2.5 0 1.2 3.2-1.6 1.2a8 8 0 0 0 4.5 4.5l1.2-1.6 3.2 1.2v2.5c0 .8-.7 1.5-1.5 1.5C7 14 2 9 2 3c0-.8.7-1.5 1.5-1.5z"/></svg>
      <svg style="top:83px" viewBox="0 0 16 16"><path d="M4.5 1h7v14h-7zM6 2.5v9.5h4V2.5zM7.3 13h1.4v1H7.3z" fill-rule="evenodd"/></svg>
      <svg style="top:102px" viewBox="0 0 16 16"><path d="M4 1h8v4H4zM1 6h14v6h-3v3H4v-3H1zm4 4v4h6v-4z" fill-rule="evenodd"/></svg>
      <svg style="top:121px" viewBox="0 0 16 16"><path d="M1 3.5h14v9H1zm1.5 1.2L8 8.8l5.5-4.1z"/></svg>
      <svg style="top:140px" viewBox="0 0 16 16"><circle cx="8" cy="8" r="6.5"/><path d="M5 5.5c1 0 1.5 1 2.5 1s.5 2-1 2.5-.5 2.5-2 2.5M10.5 4c-.5 1 .5 2 1.5 2M10 10.5c.5-1 2-1 2.5-.5" stroke="#c8161d" stroke-width="1.1" fill="none"/></svg>
    </div>
    <div class="contact-list">
      <p class="address">Level 1, 47 Fernby Street<br>Carlow Qld 4072</p>
      <p>+61 (0)7 3880 4120</p>
      <p>+61 (0)7 3880 4127</p>
      <p>+61 (0)412 560 398</p>
      <p>+61 (0)7 3880 4199</p>
      <p>mwhitfield@korvalit.com.au</p>
      <p>www.korvalit.com.au</p>
    </div>
    <div class="person">
      <p class="person-name">MARA WHITFIELD</p>
      <p class="person-title">Business Development Manager</p>
    </div>
  </section>

  <section class="card card-back" aria-label="Card back">
    <div class="back-brand">
      <span class="brand-square"></span>
      <span class="brand-name">korvalIT</span>
    </div>
    <div class="service-row">
      <span class="service"><span class="service-square"></span>MapOut</span>
      <span class="service"><span class="service-square"></span>ShipWell</span>
      <span class="service"><span class="service-square"></span>KeepSteady</span>
    </div>
  </section>
</main>
</body>
</html>
```